Letterhead & Greeting Card Design Project

I need a few files prepared for dynamic digital printing: letterhead and 2 postcards with an envelope for each. Enclosed are specific directions from the printer for each file and overall. I have also enclosed mockups of what I would like on those designs and some raw files to work with.

Industry/Entity Type

Digital

```html
<!DOCTYPE html>
<html lang="en">
<head>
<meta charset="UTF-8">
<title>Be an Ad Star – Card</title>
<link rel="stylesheet" href="https://fonts.googleapis.com/css2?family=Titillium+Web:wght@400;700&display=swap">
<style>
  :root {
    --paper: #ffffff;
    --ink: #1c1c1c;
    --brand-blue: #1a98cf;
    --star-grey: #646464;
    --fold-line: #a8d9ec;
  }
  * { margin: 0; padding: 0; box-sizing: border-box; }
  html, body {
    width: 826px;
    height: 1200px;
    overflow: hidden;
    background: var(--paper);
  }
  .card {
    position: relative;
    width: 826px;
    height: 1200px;
    background: var(--paper);
    font-family: "Titillium Web", Arial, sans-serif;
    color: var(--ink);
  }
  .card-guides {
    position: absolute;
    inset: 0;
  }
  .headline {
    position: absolute;
    top: 250px;
    left: 0;
    width: 100%;
    text-align: center;
    font-weight: 700;
    font-size: 107px;
    line-height: 1;
    letter-spacing: -0.5px;
    white-space: nowrap;
    color: var(--ink);
  }
  .headline .accent-blue { color: var(--brand-blue); }
  .headline .accent-grey { color: var(--star-grey); }
  .message {
    position: absolute;
    left: 108px;
    font-size: 36px;
    line-height: 49px;
    font-weight: 400;
    white-space: nowrap;
  }
  .greeting { top: 710px; }
  .body-text { top: 790px; }
  .closing { top: 868px; }
  .postscript { top: 996px; }
</style>
</head>
<body>
  <main class="card">
    <svg class="card-guides" width="826" height="1200" viewBox="0 0 826 1200" aria-hidden="true">
      <rect class="card-frame" x="52" y="51" width="722" height="1104" rx="4" fill="none" stroke="var(--brand-blue)" stroke-width="4"/>
      <line class="fold-line" x1="0" y1="600" x2="826" y2="600" stroke="var(--fold-line)" stroke-width="2"/>
    </svg>

    <h1 class="headline">Be an <span class="accent-blue">Ad</span> <span class="accent-grey">Star</span></h1>

    <p class="message greeting">Greating</p>
    <p class="message body-text">Body Text Goes Here</p>
    <p class="message closing">Closing,<br>First Name</p>
    <p class="message postscript">P.S. Goes Here</p>
  </main>
</body>
</html>
```